Business Card Design - Photographer

I am a landscape photographer and I require a business card design. 

I require two designs:
1)  a double sided business card
 and
b)  a single sided business card 

The single sided design can either be the same as the double sided (with just one side having all the information)....or it can be an entire new design. Its up to you.

My corporate colours are (CMYK):

Blue   69, 32, 0, 0
Grey  72,  64,  47,  31
Green  32,  2,  91,  0
Yellow   0, 19, 92, 0
Orange  0, 39, 75, 0

Colour space in final file should be in CMYK.

The details that need to be included on the card:

- Use the provided Logo
- Name: Wiktor Baranowski
- Email:   sales@vistalumeworks.com.au
- Website:    vistalumeworks.com.au
- Twitter:    twitter.com/vistalumeworks
- Facebook:   facebook.com/vistalumeworks
- Mobile  0417 539 662

Please use the attached template to design the logo to the specified size, including the marked bleed lines. I have also attached my logo in PNG (transparent background) and ai format for you to use.

The final file should be:
- Photoshop version with layers so I can edit the name/text etc. All non vector files should be high resolution at 1039 x 697 pixels at 300 dpi.

I also require a file as:
- Vector based PDF

Anyway questions please contact me.

Thank you

Industry/Entity Type

Landscape

Logo styles of interest
Pictorial/Combination Logo
Abstract Logo
Wordmark Logo
Lettermark Logo
Requirements
Must have
• The details that need to be included on the card:

- Use the provided Logo
- Name: Wiktor Baranowski
- Email: sales@vistalumeworks.com.au
- Website: vistalumeworks.com.au
- Twitter: twitter.com/vistalumeworks
- Facebook: facebook.com/vistalumeworks
- Mobile 0417 539 662

```html
<!DOCTYPE html>
<html lang="en">
<head>
<meta charset="utf-8">
<title>Vistalume Works – Business Card</title>
<link rel="stylesheet" href="https://fonts.googleapis.com/css2?family=Cinzel:wght@500;600&family=Tinos:wght@400;700&family=Montserrat:wght@400&display=swap">
<style>
  :root {
    --stage: #e9e6e1;
    --paper: #ffffff;
    --slate: #3d3f52;
    --ink: #4a4a4a;
    --blue: #3f8ccb;
    --orange: #f7a743;
    --rule: #b9b9b9;
    --white: #ffffff;
  }
  html, body {
    margin: 0;
    padding: 0;
    overflow: hidden;
  }
  .canvas {
    position: relative;
    width: 1200px;
    height: 374px;
    background: var(--stage);
    overflow: hidden;
  }
  .card {
    position: absolute;
    top: 33px;
    width: 524px;
    height: 300px;
    overflow: hidden;
    box-shadow: 0 2px 6px rgba(0,0,0,0.25);
  }
  .card--front { left: 53px; background: var(--paper); }
  .card--back { left: 611px; width: 525px; background: var(--slate); }

  .brand {
    position: absolute;
    top: 55px;
    display: flex;
    flex-direction: column;
    align-items: center;
  }
  .brand__dot {
    width: 90px;
    height: 90px;
    border-radius: 50%;
  }
  .brand__lockup {
    display: flex;
    flex-direction: column;
    align-items: stretch;
    text-align: center;
  }
  .brand__name {
    font-family: "Cinzel", serif;
    font-weight: 600;
    white-space: nowrap;
    line-height: 1;
  }
  .brand__rule {
    height: 1px;
    margin-top: 4px;
  }
  .brand__tagline {
    margin-top: 6px;
    font-family: "Cinzel", serif;
    font-weight: 600;
    font-size: 9px;
    letter-spacing: 2.4px;
    white-space: nowrap;
    line-height: 1;
  }

  .card--front .brand { left: 0; width: 276px; }
  .card--front .brand__dot { background: var(--slate); }
  .card--front .brand__lockup { margin-top: 8px; }
  .card--front .brand__name { font-size: 23px; letter-spacing: 0.3px; color: var(--slate); }
  .card--front .brand__rule { background: var(--slate); }
  .card--front .brand__tagline { color: var(--slate); }

  .card--back .brand { left: 0; width: 525px; }
  .card--back .brand__dot { width: 94px; height: 94px; background: var(--white); }
  .card--back .brand__lockup { margin-top: 19px; }
  .card--back .brand__name { font-size: 26px; letter-spacing: 0.4px; color: var(--white); }
  .card--back .brand__rule { background: var(--white); margin-top: 5px; }
  .card--back .brand__tagline { color: var(--white); font-size: 10px; letter-spacing: 2.8px; margin-top: 7px; }

  .divider {
    position: absolute;
    left: 278px;
    top: 40px;
    width: 1px;
    height: 156px;
    background: var(--rule);
  }
  .contact {
    position: absolute;
    left: 295px;
    top: 44px;
    margin: 0;
    padding: 0;
    list-style: none;
    font-family: "Tinos", serif;
    font-size: 14px;
    line-height: 19px;
    color: var(--ink);
  }
  .contact__person {
    font-weight: 700;
    color: var(--slate);
    margin-bottom: 3px;
  }
  .contact__address { margin-bottom: 11px; }
  .contact__item {
    display: flex;
    align-items: center;
    gap: 5px;
  }
  .contact__icon {
    width: 9px;
    height: 9px;
    flex: none;
  }
  .contact__mark {
    width: 8px;
    height: 8px;
    flex: none;
    background: #6a6a6a;
    border-radius: 1px;
  }

  .waves {
    position: absolute;
    left: 0;
    bottom: 0;
    width: 524px;
    height: 300px;
  }
  .web { position: absolute; white-space: nowrap; }
  .card--front .web {
    right: 22px;
    bottom: 16px;
    color: var(--white);
    font-family: "Tinos", serif;
    font-size: 14px;
    letter-spacing: 1.7px;
  }
  .card--back .web {
    left: 0;
    width: 525px;
    text-align: center;
    top: 246px;
    color: var(--white);
    font-family: "Montserrat", sans-serif;
    font-size: 13px;
    letter-spacing: 1.6px;
  }
</style>
</head>
<body>
<main class="canvas">
  <section class="card card--front">
    <svg class="waves" viewBox="0 0 524 300" aria-hidden="true">
      <path d="M0,268 C150,268 260,232 524,238 L524,300 L0,300 Z" fill="var(--orange)"/>
      <path d="M0,287 C170,282 300,224 524,233 L524,300 L0,300 Z" fill="var(--white)"/>
      <path d="M0,292 C170,286 320,230 524,237 L524,300 L0,300 Z" fill="var(--slate)"/>
      <path d="M0,259 C140,262 260,214 524,236" fill="none" stroke="var(--blue)" stroke-width="5"/>
    </svg>

    <div class="brand">
      <div class="brand__dot"></div>
      <div class="brand__lockup">
        <div class="brand__name">VISTALUME WORKS</div>
        <div class="brand__rule"></div>
        <div class="brand__tagline">FINE ART PHOTOGRAPHY</div>
      </div>
    </div>

    <div class="divider"></div>

    <ul class="contact">
      <li class="contact__person">Wiktor Baranowski</li>
      <li class="contact__address">00, Complex Name<br>State Name, City 0020</li>
      <li class="contact__item">
        <svg class="contact__icon" viewBox="0 0 10 10" aria-hidden="true"><rect x="2.5" y="0.5" width="5" height="9" rx="1" fill="#6a6a6a"/><rect x="3.5" y="1.8" width="3" height="4.5" fill="#fff"/></svg>
        0417 539 662
      </li>
      <li class="contact__item"><span class="contact__mark"></span>vistalumeworks</li>
      <li class="contact__item"><span class="contact__mark"></span>vistalumeworks</li>
      <li class="contact__item">
        <svg class="contact__icon" viewBox="0 0 10 10" aria-hidden="true"><rect x="0" y="2" width="10" height="7" fill="#6a6a6a"/><path d="M0,2 L5,6 L10,2" fill="none" stroke="#fff" stroke-width="1"/></svg>
        sales@vistalumeworks.com.au
      </li>
    </ul>

    <div class="web">www.vistalumeworks.com.au</div>
  </section>

  <section class="card card--back">
    <div class="brand">
      <div class="brand__dot"></div>
      <div class="brand__lockup">
        <div class="brand__name">VISTALUME WORKS</div>
        <div class="brand__rule"></div>
        <div class="brand__tagline">FINE ART PHOTOGRAPHY</div>
      </div>
    </div>
    <div class="web">www.vistalumeworks.com.au</div>
  </section>
</main>
</body>
</html>
```